Real Estate Business Card

On the front side I want to have my info, my brokerage info.
On the back side I want have my complany’s logo, website and Facebook link. I will provide all this once I select a design.

I would like to see Black background and gold text, Dark Blue and gold text and White and blue text designs

Font styles to use
Sans Serif
Script

```html
<!DOCTYPE html>
<html lang="en">
<head>
<meta charset="UTF-8">
<title>Northwall Real Estate – Business Card</title>
<link rel="stylesheet" href="https://fonts.googleapis.com/css2?family=Montserrat:wght@700;800&family=Roboto:wght@400;500&display=swap">
<style>
  :root {
    --backdrop: #d9d9d9;
    --card: #1e1e1f;
    --gold: #e8c23a;
    --gold-soft: #d9b22e;
    --steel: #4d5563;
    --white: #f2f2f2;
    --rule: #6a6a6a;
  }
  * { margin: 0; padding: 0; box-sizing: border-box; }
  html, body {
    width: 1200px; height: 900px; overflow: hidden;
    background: var(--backdrop);
  }
  .stage {
    width: 1200px; height: 900px;
    display: flex; flex-direction: column;
    align-items: center; justify-content: center; gap: 60px;
  }
  .card {
    width: 600px; height: 343px;
    background: var(--card);
    border-radius: 3px;
    box-shadow: 0 6px 18px rgba(0,0,0,.25);
    position: relative;
  }
  /* Logo side */
  .card--brand {
    display: flex; align-items: center; justify-content: center;
  }
  .brand-lockup {
    display: flex; align-items: center; gap: 16px;
  }
  .brand-square {
    width: 46px; height: 46px; background: var(--steel);
  }
  .brand-name {
    font-family: "Montserrat", sans-serif;
    font-weight: 800;
    font-size: 40px;
    letter-spacing: 1px;
    color: var(--steel);
    text-transform: uppercase;
    line-height: 1;
  }
  /* Info side */
  .card--info {
    display: flex; justify-content: space-between; align-items: center;
    padding: 0 56px 0 60px;
  }
  .contact { display: flex; flex-direction: column; }
  .person-name {
    font-family: "Roboto", sans-serif; font-weight: 500;
    font-size: 24px; color: var(--gold);
    text-transform: uppercase; letter-spacing: .5px;
  }
  .person-role {
    font-family: "Roboto", sans-serif; font-weight: 500;
    font-size: 16px; color: var(--white);
    text-transform: uppercase; margin-top: 2px;
  }
  .divider {
    width: 70px; border-top: 2px dotted var(--rule);
    margin: 16px 0 14px;
  }
  .address, .details li {
    font-family: "Roboto", sans-serif; font-weight: 400;
    font-size: 15px; color: var(--white); line-height: 1.45;
  }
  .address { margin-bottom: 12px; }
  .details { list-style: none; }
  .details li { display: flex; align-items: center; gap: 9px; }
  .details svg { width: 13px; height: 13px; flex: none; }
  .social {
    position: absolute; left: 60px; bottom: 30px;
    display: flex; align-items: center; gap: 9px;
    font-family: "Roboto", sans-serif; font-size: 15px; color: var(--white);
  }
  .social-square { width: 13px; height: 13px; background: var(--gold); }
  .brand-mark {
    font-family: "Montserrat", sans-serif; font-weight: 800;
    font-size: 34px; color: var(--gold-soft);
    text-transform: uppercase; letter-spacing: 1px;
    align-self: center; margin-top: -40px;
  }
</style>
</head>
<body>
<main class="stage">
  <section class="card card--brand" aria-label="Card front">
    <div class="brand-lockup">
      <span class="brand-square"></span>
      <span class="brand-name">Northwall Real Estate</span>
    </div>
  </section>

  <section class="card card--info" aria-label="Card back">
    <div class="contact">
      <h1 class="person-name">Daniel Hart</h1>
      <p class="person-role">CEO/Founder</p>
      <div class="divider"></div>
      <p class="address">4120 Juniper Court<br>Fairbanks, Alaska 99701</p>
      <ul class="details">
        <li>
          <svg viewBox="0 0 16 16"><path fill="var(--gold)" d="M4 1l3 3-2 2c1 2 3 4 5 5l2-2 3 3-2 3C7 15 1 9 1 3z"/></svg>
          555 214 7390
        </li>
        <li>
          <svg viewBox="0 0 16 16"><rect x="1" y="3" width="14" height="10" fill="var(--gold)"/><path d="M1 3l7 6 7-6" stroke="var(--card)" stroke-width="1.5" fill="none"/></svg>
          daniel@northwallre.com
        </li>
        <li>
          <svg viewBox="0 0 16 16"><circle cx="8" cy="8" r="7" fill="var(--gold)"/><path d="M1 8h14M8 1c-3 4-3 10 0 14M8 1c3 4 3 10 0 14" stroke="var(--card)" stroke-width="1.2" fill="none"/></svg>
          www.northwallre.com
        </li>
      </ul>
    </div>
    <div class="social"><span class="social-square"></span>/northwallre</div>
    <div class="brand-mark">Northwall</div>
  </section>
</main>
</body>
</html>
```